TALMORK

The business want a professional looking business card. We have a scetch we will add but want the extra upgrade, and would like more suggestions for variations of our business cards.

```html
<!DOCTYPE html>
<html lang="en">
<head>
<meta charset="utf-8">
<title>TALMORK business card</title>
<link href="https://fonts.googleapis.com/css2?family=Montserrat:wght@400;500;600&display=swap" rel="stylesheet">
<style>
  :root {
    --backdrop: #1b1b1c;
    --card: #1f1f20;
    --card-back: #19191a;
    --gold: #d2a445;
    --gold-light: #e7c36c;
    --white: #f1f1f1;
    --emboss: #2c2c2e;
  }
  * { margin: 0; padding: 0; box-sizing: border-box; }
  html, body {
    width: 1200px; height: 801px; overflow: hidden;
    background: var(--backdrop);
    font-family: "Montserrat", sans-serif;
  }
  .canvas {
    position: relative; width: 1200px; height: 801px;
    display: flex; align-items: center; justify-content: center; gap: 48px;
  }
  .card {
    position: relative; width: 520px; height: 297px;
    border-radius: 18px;
    box-shadow: 0 18px 40px rgba(0,0,0,.55);
    overflow: hidden;
  }
  .card-front { background: var(--card); }
  .card-back { background: var(--card-back); }

  .brand {
    position: absolute; left: 40px; top: 48px;
    color: var(--gold);
  }
  .brand-name {
    display: flex; align-items: center; gap: 10px;
    font-weight: 500; font-size: 26px; letter-spacing: 6px;
  }
  .brand-dot {
    width: 12px; height: 12px; border-radius: 50%; background: var(--gold);
  }
  .brand-since {
    margin-top: 6px; margin-left: 22px;
    font-size: 8px; letter-spacing: 5px; font-weight: 500;
  }

  .holder {
    position: absolute; right: 40px; top: 44px; text-align: right;
  }
  .holder-name {
    display: flex; align-items: center; justify-content: flex-end; gap: 10px;
    color: var(--gold-light); font-weight: 600; font-size: 17px;
  }
  .holder-mark { width: 20px; height: 20px; background: var(--gold); }
  .holder-title {
    margin-top: 4px; margin-right: 30px;
    color: var(--white); font-size: 12px; font-weight: 400;
  }

  .contacts {
    position: absolute; left: 40px; bottom: 38px;
    list-style: none; display: flex; flex-direction: column; gap: 9px;
  }
  .contact {
    display: flex; align-items: center; gap: 12px;
    color: var(--white); font-size: 14px; font-weight: 400; letter-spacing: .3px;
  }
  .contact svg { width: 14px; height: 14px; fill: var(--gold); flex: none; }

  .back-brand {
    position: absolute; inset: 0;
    display: flex; flex-direction: column; align-items: center; justify-content: center;
    color: var(--emboss);
  }
  .back-brand .brand-name { font-size: 34px; letter-spacing: 9px; }
  .back-brand .brand-dot { width: 14px; height: 14px; background: var(--emboss); }
  .back-brand .brand-since { margin-left: 0; margin-top: 8px; font-size: 10px; letter-spacing: 7px; }
</style>
</head>
<body>
<main class="canvas">
  <section class="card card-front" aria-label="Business card front">
    <div class="brand">
      <div class="brand-name"><span class="brand-dot"></span>TALMORK</div>
      <div class="brand-since">SINCE 2026</div>
    </div>

    <div class="holder">
      <div class="holder-name">Anders Lykke Haugland <span class="holder-mark"></span></div>
      <div class="holder-title">CEO &amp; Founder</div>
    </div>

    <ul class="contacts">
      <li class="contact">
        <svg viewBox="0 0 24 24" aria-hidden="true"><path d="M6.6 10.8a15.1 15.1 0 0 0 6.6 6.6l2.2-2.2c.3-.3.7-.4 1-.2 1.1.4 2.3.6 3.6.6.6 0 1 .4 1 1V20c0 .6-.4 1-1 1A17 17 0 0 1 3 4c0-.6.4-1 1-1h3.5c.6 0 1 .4 1 1 0 1.3.2 2.5.6 3.6.1.3 0 .7-.2 1z"/></svg>
        004791836452
      </li>
      <li class="contact">
        <svg viewBox="0 0 24 24" aria-hidden="true"><path d="M3 5h18c.6 0 1 .4 1 1v12c0 .6-.4 1-1 1H3c-.6 0-1-.4-1-1V6c0-.6.4-1 1-1zm9 7.5L20 7H4z"/></svg>
        talmork.llc@postmail.com
      </li>
      <li class="contact">
        <svg viewBox="0 0 24 24" aria-hidden="true"><path d="M12 2a10 10 0 1 0 0 20 10 10 0 0 0 0-20zm6.9 6h-3a15 15 0 0 0-1.3-3.9A8 8 0 0 1 18.9 8zM12 4c.8 1.2 1.5 2.5 1.9 4h-3.8c.4-1.5 1.1-2.8 1.9-4zM4.3 14a8 8 0 0 1 0-4h3.4a16 16 0 0 0 0 4zm.8 2h3a15 15 0 0 0 1.3 3.9A8 8 0 0 1 5.1 16zm3-8h-3a8 8 0 0 1 4.3-3.9A15 15 0 0 0 8.1 8zM12 20c-.8-1.2-1.5-2.5-1.9-4h3.8c-.4 1.5-1.1 2.8-1.9 4zm2.3-6H9.7a14 14 0 0 1 0-4h4.6a14 14 0 0 1 0 4zm.3 5.9a15 15 0 0 0 1.3-3.9h3a8 8 0 0 1-4.3 3.9zm1.7-5.9a16 16 0 0 0 0-4h3.4a8 8 0 0 1 0 4z"/></svg>
        www.talmork.llc
      </li>
    </ul>
  </section>

  <section class="card card-back" aria-label="Business card back">
    <div class="back-brand">
      <div class="brand-name"><span class="brand-dot"></span>TALMORK</div>
      <div class="brand-since">SINCE 2026</div>
    </div>
  </section>
</main>
</body>
</html>
```